Create a new business card

I’m looking to update my business card to make it match the rest of my brand. I will include my current website as well as what my vehicle designs look like, etc..
What my business currently services
Weekly maintenance pool openings / closings
Equipment repair, including pumps, heaters, salt systems, filters, etc.
We install automatic covers and maintain them as well as provide preventative maintenance

I would like to include my name.
Dorian Pelkin.
My title
Owner
My email
Dorian@tidewellnx.com
4015827160
Www.tidewellnx.com

```html
<!DOCTYPE html>
<html lang="en">
<head>
<meta charset="utf-8">
<title>Tidewell Pool Service – Business Card</title>
<link href="https://fonts.googleapis.com/css2?family=Montserrat:wght@400;500;600;800&display=swap" rel="stylesheet">
<style>
  :root {
    --backdrop: #b9babc;
    --navy: #232d63;
    --sky: #3ab0e6;
    --paper: #ffffff;
    --water-deep: #1f6fae;
    --water-mid: #2f94d2;
    --water-light: #48b6e8;
    --heading-blue: #5cc3f0;
    --ink: #2a2f45;
  }
  * { box-sizing: border-box; margin: 0; padding: 0; }
  html, body { width: 1200px; height: 900px; overflow: hidden; }
  body {
    background: var(--backdrop);
    font-family: "Montserrat", sans-serif;
    display: flex;
    flex-direction: column;
    align-items: center;
    justify-content: center;
    gap: 34px;
  }
  .card {
    position: relative;
    width: 700px;
    height: 400px;
    border-radius: 22px;
    overflow: hidden;
    box-shadow: 0 8px 22px rgba(0,0,0,0.18);
  }

  /* Front */
  .card-front { background: var(--paper); }
  .card-front .swoosh { position: absolute; inset: 0; width: 100%; height: 100%; }
  .brand-mark {
    position: absolute;
    display: flex;
    align-items: center;
    gap: 14px;
  }
  .card-front .brand-mark { left: 40px; top: 120px; width: 240px; }
  .brand-dot {
    flex: 0 0 auto;
    width: 46px; height: 46px;
    border-radius: 50%;
    background: var(--sky);
  }
  .brand-name {
    font-weight: 800;
    font-size: 25px;
    line-height: 1.12;
    color: var(--navy);
  }
  .divider {
    position: absolute;
    width: 2px;
  }
  .card-front .divider { left: 298px; top: 92px; height: 150px; background: var(--navy); }
  .contact-block { position: absolute; left: 326px; top: 86px; color: var(--ink); }
  .person-name { font-weight: 800; font-size: 27px; color: var(--navy); letter-spacing: 0.2px; }
  .person-title { font-size: 15px; margin-top: 2px; margin-bottom: 16px; }
  .contact-list { list-style: none; }
  .contact-list li {
    display: flex; align-items: center; gap: 10px;
    font-size: 15px; margin-bottom: 7px;
  }
  .contact-list svg { width: 15px; height: 15px; fill: var(--sky); flex: 0 0 auto; }

  /* Back */
  .card-back {
    background:
      radial-gradient(ellipse at 30% 70%, rgba(120,210,245,0.35), transparent 60%),
      linear-gradient(160deg, var(--water-deep) 0%, var(--water-mid) 50%, var(--water-light) 100%);
  }
  .water-texture { position: absolute; inset: 0; }
  .card-back .brand-mark { left: 48px; top: 150px; width: 270px; }
  .card-back .brand-dot { background: rgba(255,255,255,0.9); width: 52px; height: 52px; }
  .card-back .brand-name { color: var(--paper); font-size: 28px; }
  .card-back .divider { left: 370px; top: 70px; height: 240px; background: rgba(255,255,255,0.75); width: 1.5px; }
  .services { position: absolute; left: 398px; top: 78px; color: var(--paper); }
  .services-heading {
    font-weight: 800; font-size: 25px; color: var(--heading-blue);
    letter-spacing: 0.5px; margin-bottom: 10px;
  }
  .services-list { list-style: none; }
  .services-list li {
    font-size: 16px; font-weight: 500; margin-bottom: 8px;
    padding-left: 16px; position: relative; white-space: nowrap;
  }
  .services-list li::before {
    content: ""; position: absolute; left: 0; top: 8px;
    width: 6px; height: 6px; border-radius: 50%; background: var(--paper);
  }
</style>
</head>
<body>

  <section class="card card-front" aria-label="Business card front">
    <svg class="swoosh" viewBox="0 0 700 400" preserveAspectRatio="none" aria-hidden="true">
      <path d="M0,342 C240,338 500,288 612,160 C652,114 682,64 700,22 L700,400 L0,400 Z" fill="var(--sky)"/>
      <path d="M0,345 C240,343 502,298 620,174 C660,130 688,82 700,46 L700,400 L0,400 Z" fill="var(--paper)"/>
      <path d="M0,351 C245,350 506,306 627,182 C666,138 690,92 700,62 L700,400 L0,400 Z" fill="var(--navy)"/>
    </svg>

    <div class="brand-mark">
      <span class="brand-dot"></span>
      <span class="brand-name">Tidewell Pool Service</span>
    </div>

    <span class="divider"></span>

    <div class="contact-block">
      <h1 class="person-name">Dorian Pelkin</h1>
      <p class="person-title">Owner</p>
      <ul class="contact-list">
        <li>
          <svg viewBox="0 0 24 24" aria-hidden="true"><path d="M6.6 10.8a15.1 15.1 0 0 0 6.6 6.6l2.2-2.2a1 1 0 0 1 1-.25 11.4 11.4 0 0 0 3.6.57 1 1 0 0 1 1 1V20a1 1 0 0 1-1 1A17 17 0 0 1 3 4a1 1 0 0 1 1-1h3.5a1 1 0 0 1 1 1c0 1.25.2 2.45.57 3.57a1 1 0 0 1-.25 1z"/></svg>
          4015827160
        </li>
        <li>
          <svg viewBox="0 0 24 24" aria-hidden="true"><path d="M2 5h20v14H2z M2 5l10 8 10-8" fill="none" stroke="var(--sky)" stroke-width="2.4"/></svg>
          Dorian@tidewellnx.com
        </li>
        <li>
          <svg viewBox="0 0 24 24" aria-hidden="true"><circle cx="12" cy="12" r="9" fill="none" stroke="var(--sky)" stroke-width="2.4"/><path d="M3 12h18M12 3c3 3.5 3 14.5 0 18M12 3c-3 3.5-3 14.5 0 18" fill="none" stroke="var(--sky)" stroke-width="1.8"/></svg>
          Www.tidewellnx.com
        </li>
      </ul>
    </div>
  </section>

  <section class="card card-back" aria-label="Business card back">
    <div class="water-texture" role="img" aria-label="Rippling pool water photograph in bright blue tones"></div>

    <div class="brand-mark">
      <span class="brand-dot"></span>
      <span class="brand-name">Tidewell Pool Service</span>
    </div>

    <span class="divider"></span>

    <div class="services">
      <h2 class="services-heading">OUR SERVICES</h2>
      <ul class="services-list">
        <li>Weekly pool maintenance</li>
        <li>Pool Openings and Closings</li>
        <li>Pump, heater and filter repair</li>
        <li>Salt system repair</li>
        <li>Automatic cover installs</li>
        <li>Preventative maintenance</li>
      </ul>
    </div>
  </section>

</body>
</html>
```